Shine Fox Auto Care Business Card

2 side business card design for an auto detailing business

Target Market(s)

Auto detailing

Contact Information for Business Card

Things included

The business name “Shine Fox Auto Care”
Mark Dunrow
(403)271-6094
Pinecrest, Sk

Services offered - complete interior& exterior detail
- paint correction & protection
- ceramic coating
- trim restore
- auto carpet & seat cleaning

Requirements
Must have
• Colours that are in my logo

Services offered

My name Mark Dunrow
403-271-6094
Pinecrest, Sk

Not too sure in what order for these ?
Website. Shinefoxautocare.com
Instagram Shinefoxautocare
Email. Shinefoxautoac@mailvento.com

```html
<!DOCTYPE html>
<html lang="en">
<head>
<meta charset="utf-8">
<title>Shine Fox Auto Care – Business Card</title>
<link rel="stylesheet" href="https://fonts.googleapis.com/css2?family=Open+Sans:wght@400;600;700&display=swap">
<style>
  :root {
    --bg: #3a3a3a;
    --card: #1c1c1c;
    --red: #a5191c;
    --white: #f2f2f2;
  }
  * { margin: 0; padding: 0; box-sizing: border-box; }
  html, body { width: 1200px; height: 801px; overflow: hidden; }
  body {
    background: radial-gradient(circle at 50% 40%, #474747, var(--bg) 70%);
    font-family: "Open Sans", Arial, sans-serif;
    display: flex;
    align-items: center;
    justify-content: center;
    gap: 60px;
  }
  .card {
    position: relative;
    width: 525px;
    height: 300px;
    background: var(--card);
    border-bottom: 3px solid var(--red);
    border-right: 2px solid var(--red);
    box-shadow: 0 14px 30px rgba(0,0,0,.45);
    overflow: hidden;
    color: var(--white);
  }
  .brand {
    position: absolute;
    display: flex;
    align-items: center;
    gap: 12px;
  }
  .brand-dot {
    width: 40px; height: 40px;
    border-radius: 50%;
    background: var(--red);
    flex: none;
  }
  .brand-name {
    font-weight: 700;
    font-size: 22px;
    line-height: 1.1;
    color: var(--white);
    letter-spacing: .5px;
  }
  .front .brand { left: 34px; top: 118px; width: 210px; }
  .divider {
    position: absolute;
    left: 258px; top: 60px;
    width: 1.5px; height: 180px;
    background: var(--red);
  }
  .contact { position: absolute; left: 284px; top: 66px; }
  .person-name {
    color: var(--red);
    font-weight: 700;
    font-size: 19px;
    letter-spacing: .5px;
  }
  .person-role { font-size: 14px; margin-bottom: 12px; }
  .contact-list { list-style: none; }
  .contact-list li {
    display: flex; align-items: center; gap: 8px;
    font-size: 13px; line-height: 22px;
  }
  .contact-list svg { width: 12px; height: 12px; fill: var(--red); flex: none; }
  .back-mark {
    position: absolute;
    right: -70px; top: -40px;
    width: 300px; height: 300px;
    border-radius: 50%;
    background: radial-gradient(circle at 40% 40%, #2a2a2a, #101010 75%);
  }
  .back .brand { left: 38px; top: 58px; }
  .services {
    position: absolute; left: 40px; top: 140px;
    list-style: none;
    font-size: 15px; line-height: 26px;
  }
</style>
</head>
<body>
  <section class="card front" aria-label="Card front">
    <div class="brand">
      <span class="brand-dot"></span>
      <span class="brand-name">Shine Fox Auto Care</span>
    </div>
    <div class="divider"></div>
    <div class="contact">
      <p class="person-name">MARK DUNROW</p>
      <p class="person-role">President</p>
      <ul class="contact-list">
        <li><svg viewBox="0 0 24 24"><path d="M6.6 10.8a15 15 0 0 0 6.6 6.6l2.2-2.2c.3-.3.7-.4 1-.2 1.1.4 2.3.6 3.6.6.6 0 1 .4 1 1V20c0 .6-.4 1-1 1A17 17 0 0 1 3 4c0-.6.4-1 1-1h3.5c.6 0 1 .4 1 1 0 1.3.2 2.5.6 3.6.1.3 0 .7-.2 1z"/></svg>403-271-6094</li>
        <li><svg viewBox="0 0 24 24"><path d="M2 5h20v14H2zm2 2v.5l8 5 8-5V7l-8 5z"/></svg>Shinefoxautoac@mailvento.com</li>
        <li><svg viewBox="0 0 24 24"><path d="M12 2a10 10 0 1 0 0 20 10 10 0 0 0 0-20zm-1 17.9A8 8 0 0 1 4.1 11H8c.1 3 1.1 6 3 8.9zM4.1 9A8 8 0 0 1 11 4.1C9.1 7 8.1 9 8 9zm9.9 10.9c1.9-2.9 2.9-5.9 3-8.9h3.9a8 8 0 0 1-6.9 8.9zM16 9c-.1 0-1.1-2-3-4.9A8 8 0 0 1 19.9 9z"/></svg>Shinefoxautocare.com</li>
        <li><svg viewBox="0 0 24 24"><circle cx="12" cy="12" r="9"/></svg>Shinefoxautocare</li>
        <li><svg viewBox="0 0 24 24"><path d="M12 2a7 7 0 0 0-7 7c0 5 7 13 7 13s7-8 7-13a7 7 0 0 0-7-7zm0 9.5a2.5 2.5 0 1 1 0-5 2.5 2.5 0 0 1 0 5z"/></svg>Pinecrest, Sk</li>
      </ul>
    </div>
  </section>

  <section class="card back" aria-label="Card back">
    <div class="back-mark" role="img" aria-label="Large glossy brand mark decoration"></div>
    <div class="brand">
      <span class="brand-dot"></span>
      <span class="brand-name">Shine Fox Auto Care</span>
    </div>
    <ul class="services">
      <li>complete interior&amp; exterior detail</li>
      <li>paint correction &amp; protection</li>
      <li>ceramic coating</li>
      <li>trim restore</li>
      <li>auto carpet &amp; seat cleaning</li>
    </ul>
  </section>
</body>
</html>
```